Website for "Nodo de Soluciones Verdantes"

We need a new web design for an enterprise dedicated to environment and energy saving engineering, based in Monterrey, Mexico.
They offer consulting services, mainly to enhance building designs, and they are also resellers for several products in the energy saving field.

The final design should be oriented to engineers and architects, and should communicate professionalism, innovation, environment care.

Here is the website of a partner enterprise, which does pretty much the same:

http://www.cirelumen.com/

Target Market(s)

mainly architects and engineers looking for solutions on energy efficiency building

Industry/Entity Type

Environment

Requirements
Must have
• Entry page must be quite graphical and intuitive, must have a "products listing" and a "projects portfolio".

```html
<!DOCTYPE html>
<html lang="en">
<head>
<meta charset="utf-8">
<title>Nodo de Soluciones Verdantes</title>
<link href="https://fonts.googleapis.com/css2?family=Bebas+Neue&family=Open+Sans:wght@400;600;700&display=swap" rel="stylesheet">
<style>
:root{
  --orange:#f47a20;
  --nav:#4b4b4d;
  --ink:#333;
  --text:#555;
  --muted:#777;
  --panel:#f2f2f2;
  --footer:#efefef;
  --line:#dcdcdc;
  --white:#fff;
}
*{margin:0;padding:0;box-sizing:border-box}
html,body{width:814px;height:1200px;overflow:hidden;background:var(--white)}
body{position:relative;font-family:"Open Sans",Arial,sans-serif;color:var(--text)}
.abs{position:absolute}

/* brand */
.brand{left:70px;top:42px;display:flex;align-items:center;gap:10px}
.brand-dot{width:44px;height:44px;border-radius:50%;background:var(--orange)}
.brand-name{font-weight:700;font-size:15px;line-height:18px;color:#4a4a4a;width:150px}

/* nav */
.nav{left:70px;top:114px;width:673px;height:40px;background:var(--nav);border-bottom:4px solid var(--orange)}
.nav ul{list-style:none;display:flex;height:36px;align-items:center;margin-left:10px}
.nav li{font-family:"Bebas Neue",Impact,sans-serif;font-size:14px;color:var(--white);padding:0 8px;line-height:36px;white-space:nowrap}
.nav li.active{background:var(--orange);padding:0 14px;margin-right:0}
.search{left:488px;top:10px;width:175px;height:19px;background:var(--white);border:1px solid #ccc;font-size:6px;color:#aaa;padding:5px 6px}
.search svg{position:absolute;right:5px;top:4px}

/* hero */
.hero{left:70px;top:160px;width:673px;height:277px;background:linear-gradient(180deg,#3f8fd6 0%,#8cc6f0 45%,#7fc04a 62%,#4c9a1f 100%)}
.hero-title{left:30px;top:196px;font-family:"Bebas Neue",Impact,sans-serif;line-height:26px}
.hero-title .l1{font-size:28px;color:var(--white)}
.hero-title .l2{font-size:36px;color:#2f2f2f;line-height:30px}
.dots{right:11px;bottom:14px;display:flex;gap:3px}
.dots span{width:8px;height:8px;border-radius:50%;background:#333;border:1px solid #333}
.dots span.on{background:var(--white)}

/* welcome */
.welcome-title{left:0;width:814px;top:452px;text-align:center;font-family:"Bebas Neue",Impact,sans-serif;font-size:17px;font-weight:400;color:#444}
.welcome-text{left:72px;width:670px;top:489px;text-align:center;font-size:8.8px;line-height:17px;color:#333}

/* panels */
.panel{top:561px;height:372px;width:220px;background:var(--panel)}
.panel-title{left:22px;top:18px;font-family:"Bebas Neue",Impact,sans-serif;font-size:18px;font-weight:400;color:#4a4a4a}
.pager{top:19px;display:flex;gap:3px}
.pager svg{display:block}
.item-title{font-size:9px;font-weight:600;color:#333}
.item-text{font-size:7.3px;line-height:12.4px;color:#666;text-align:justify}
.read{font-size:7.5px;font-weight:700;color:#222;text-align:right}

/* footer */
.footer{left:0;top:942px;width:814px;height:258px;background:var(--footer)}
.f-head{font-family:"Bebas Neue",Impact,sans-serif;font-size:13px;font-weight:400;color:#333}
.f-list{list-style:none;font-size:8.6px;color:#222}
.field{width:157px;height:19px;background:var(--white);border:1px solid #ddd;font-size:6.5px;color:#aaa;padding:5px 9px}
.subscribe{width:70px;height:17px;border-radius:9px;background:var(--orange);color:var(--white);font-size:8.5px;font-weight:600;text-align:center;line-height:17px}
.social{width:20px;height:20px;border-radius:50%;background:var(--white);border:1px solid #ddd}
.social-name{font-size:8.6px;color:#222;text-align:right;width:80px}
.rule{left:0;top:217px;width:814px;height:1px;background:var(--line)}
.copyright{left:0;width:814px;top:228px;text-align:center;font-size:8px;color:#333}
</style>
</head>
<body>

<div class="abs brand">
  <span class="brand-dot"></span>
  <span class="brand-name">Nodo de Soluciones Verdantes</span>
</div>

<nav class="abs nav">
  <ul>
    <li class="active">Home</li>
    <li>The Company</li>
    <li>Products</li>
    <li>Project Portfolio</li>
    <li>Photo Gallery</li>
    <li>News</li>
    <li>Contacts</li>
  </ul>
  <div class="abs search">Type search
    <svg width="9" height="9" viewBox="0 0 10 10"><circle cx="4" cy="4" r="3" fill="none" stroke="#999" stroke-width="1.2"/><line x1="6.2" y1="6.2" x2="9" y2="9" stroke="#999" stroke-width="1.4"/></svg>
  </div>
</nav>

<section class="abs hero" role="img" aria-label="Wind turbines on green rolling hills under a blue sky with clouds">
  <div class="abs hero-title">
    <div class="l1">Environment and Energy</div>
    <div class="l2">Saving Engineering</div>
  </div>
  <div class="abs dots"><span class="on"></span><span></span><span></span><span></span></div>
</section>

<h1 class="abs welcome-title">Welcome to Nodo</h1>
<p class="abs welcome-text">Lorem ipsum dolor sit amet, consectetur adipisicing elit, sed do eiusmod tempor incididunt ut labore et dolore magna aliqua. Ut enim ad minim veniam, quis nostrud exercitation ullamco laboris nisi ut aliquip ex ea commodo consequat. Duis aute irure dolor in reprehenderit in voluptate velit esse cillum dolore eu fugiat nulla pariatur. Excepteur sint occaecat cupidatat non proident, sunt in culpa qui officia deserunt mollit anim id est laborum.</p>

<!-- Products -->
<section class="abs panel" style="left:70px">
  <h2 class="abs panel-title">Products Listing</h2>
  <div class="abs pager" style="left:176px">
    <svg width="14" height="14" viewBox="0 0 14 14"><circle cx="7" cy="7" r="7" fill="#5b5b5b"/><path d="M8.3 4 5.3 7l3 3" fill="none" stroke="#fff" stroke-width="1.8"/></svg>
    <svg width="14" height="14" viewBox="0 0 14 14"><circle cx="7" cy="7" r="7" fill="#5b5b5b"/><path d="M5.7 4l3 3-3 3" fill="none" stroke="#fff" stroke-width="1.8"/></svg>
  </div>

  <div class="abs item-title" style="left:22px;top:56px">Energy Efficient Mixing System</div>
  <div class="abs" style="left:22px;top:75px;width:86px;height:70px;background:linear-gradient(135deg,#2c5f9e,#8fb8e0,#3a6ea8)" role="img" aria-label="Blue industrial mixing equipment"></div>
  <p class="abs item-text" style="left:112px;top:70px;width:100px">Lorem Ipsum is simply dummy text of the printing and typesetting industry. Lorem Ipsum has been the industry's standard dummy text ever .</p>
  <div class="abs read" style="left:112px;top:148px;width:100px">Read More...</div>

  <div class="abs item-title" style="left:22px;top:161px">Tube Pac Media</div>
  <div class="abs" style="left:22px;top:180px;width:86px;height:69px;background:linear-gradient(135deg,#555,#c9c2ad,#3a3a3a)" role="img" aria-label="Tube fittings and filter media"></div>
  <p class="abs item-text" style="left:112px;top:175px;width:100px">Lorem Ipsum is simply dummy text of the printing and typesetting industry. Lorem Ipsum has been the industry's standard dummy text ever .</p>
  <div class="abs read" style="left:112px;top:257px;width:100px">Read More...</div>

  <div class="abs item-title" style="left:22px;top:270px">Bio Pac Media</div>
  <div class="abs" style="left:22px;top:284px;width:86px;height:69px;background:linear-gradient(135deg,#34406a,#9aa3b5,#2a2a2a)" role="img" aria-label="Solar panels and storage tank"></div>
  <p class="abs item-text" style="left:112px;top:278px;width:100px">Lorem Ipsum is simply dummy text of the printing and typesetting industry. Lorem Ipsum has been the industry's standard dummy text ever .</p>
  <div class="abs read" style="left:112px;top:357px;width:100px">Read More...</div>
</section>

<!-- Portfolio -->
<section class="abs panel" style="left:297px">
  <h2 class="abs panel-title">Projects Portfolio</h2>
  <div class="abs pager" style="left:165px">
    <svg width="14" height="14" viewBox="0 0 14 14"><circle cx="7" cy="7" r="7" fill="#5b5b5b"/><path d="M8.3 4 5.3 7l3 3" fill="none" stroke="#fff" stroke-width="1.8"/></svg>
    <svg width="14" height="14" viewBox="0 0 14 14"><circle cx="7" cy="7" r="7" fill="#5b5b5b"/><path d="M5.7 4l3 3-3 3" fill="none" stroke="#fff" stroke-width="1.8"/></svg>
  </div>
  <div class="abs" style="left:21px;top:57px;width:178px;height:105px;background:linear-gradient(180deg,#2f7fd0,#a7d3f2 55%,#1f2c55 60%,#3b4f86)" role="img" aria-label="Solar panel field with wind turbines"></div>
  <div class="abs item-title" style="left:21px;top:172px;width:180px;font-size:9.3px;line-height:15.5px;color:#444">Sed ut perspiciatis unde omnis iste natus error sit voluptatem accusantium</div>
  <p class="abs item-text" style="left:21px;top:207px;width:180px;line-height:15px;text-align:left">Lorem Ipsum is simply dummy text of the printing and typesetting industry. Lorem Ipsum has been the industry's standard dummy text ever .</p>
  <svg class="abs" style="left:11px;top:286px" width="6" height="10" viewBox="0 0 6 10"><path d="M5 1 1 5l4 4" fill="none" stroke="#bbb" stroke-width="1.2"/></svg>
  <svg class="abs" style="left:205px;top:286px" width="6" height="10" viewBox="0 0 6 10"><path d="M1 1l4 4-4 4" fill="none" stroke="#bbb" stroke-width="1.2"/></svg>
  <div class="abs" style="left:21px;top:257px;width:86px;height:70px;background:linear-gradient(135deg,#2e66b4,#bcd8ef,#3a78c4)" role="img" aria-label="Glass solar panel reflecting sky"></div>
  <div class="abs" style="left:113px;top:257px;width:86px;height:70px;background:linear-gradient(180deg,#4a8fd6,#cfe4f4 55%,#d8c83a 80%,#7c8a2a)" role="img" aria-label="Wind turbines over a yellow field"></div>
  <p class="abs item-text" style="left:20px;top:332px;width:90px;text-align:left">Lorem Ipsum is simply dummy text</p>
  <p class="abs item-text" style="left:112px;top:332px;width:90px;text-align:left">Lorem Ipsum is simply dummy text</p>
</section>

<!-- News -->
<section class="abs panel" style="left:523px">
  <h2 class="abs panel-title">Latest News</h2>
  <div class="abs pager" style="left:170px">
    <svg width="14" height="14" viewBox="0 0 14 14"><circle cx="7" cy="7" r="7" fill="#5b5b5b"/><path d="M8.3 4 5.3 7l3 3" fill="none" stroke="#fff" stroke-width="1.8"/></svg>
    <svg width="14" height="14" viewBox="0 0 14 14"><circle cx="7" cy="7" r="7" fill="#5b5b5b"/><path d="M5.7 4l3 3-3 3" fill="none" stroke="#fff" stroke-width="1.8"/></svg>
  </div>

  <div class="abs" style="left:21px;top:57px;width:54px;height:47px;background:linear-gradient(135deg,#f2eeea,#d9c8b8)" role="img" aria-label="Scientist with a molecule diagram"></div>
  <p class="abs item-text" style="left:91px;top:55px;width:113px;line-height:14px">Lorem ipsum dolor sit amet, consectetur adipisicing elit, sed do eiusmod tempor incididunt ut labore et dolore magna aliqua.</p>
  <div class="abs item-text" style="left:91px;top:117px">May 2013 ,23rd GST 22. 10</div>

  <div class="abs" style="left:21px;top:161px;width:54px;height:47px;background:linear-gradient(135deg,#b9c3cc,#c8423a,#5f6a73)" role="img" aria-label="Engineer in red coveralls at an industrial site"></div>
  <p class="abs item-text" style="left:91px;top:159px;width:113px;line-height:14px">Lorem ipsum dolor sit amet, consectetur adipisicing elit, sed do eiusmod tempor incididunt ut labore et dolore magna aliqua.</p>
  <div class="abs item-text" style="left:91px;top:221px">May 2013 ,23rd GST 22. 10</div>

  <div class="abs" style="left:21px;top:265px;width:54px;height:47px;background:linear-gradient(135deg,#dfe6ee,#5b6a80,#2f3b4d)" role="img" aria-label="Technician working at a control station"></div>
  <p class="abs item-text" style="left:91px;top:263px;width:113px;line-height:14px">Lorem ipsum dolor sit amet, consectetur adipisicing elit, sed do eiusmod tempor incididunt ut labore et dolore magna aliqua.</p>
  <div class="abs item-text" style="left:91px;top:325px">May 2013 ,23rd GST 22. 10</div>
</section>

<!-- Footer -->
<footer class="abs footer">
  <h3 class="abs f-head" style="left:75px;top:55px">Quick Links</h3>
  <ul class="abs f-list" style="left:75px;top:82px;line-height:19.6px">
    <li>Home</li><li>The Company</li><li>Products</li><li>Portfolio</li><li>Photo Gallery</li><li>News</li><li>Contacts</li>
  </ul>

  <h3 class="abs f-head" style="left:244px;top:55px">Support Links</h3>
  <ul class="abs f-list" style="left:246px;top:83px;line-height:17px">
    <li>Legal Notice</li><li>Privacy Policy</li><li>Terms &amp; Conditions</li><li>Help</li>
  </ul>

  <h3 class="abs f-head" style="left:414px;top:55px">Newsletter Signup</h3>
  <p class="abs f-list" style="left:417px;top:78px;width:170px;line-height:14px">Sign-up for our daily emails by entering your information below:</p>
  <div class="abs field" style="left:418px;top:116px">Name</div>
  <div class="abs field" style="left:418px;top:146px">Enter Your E-Mail ID</div>
  <div class="abs subscribe" style="left:505px;top:172px">Subscribe</div>

  <h3 class="abs f-head" style="left:640px;top:55px">Connect With Us</h3>
  <span class="abs social" style="left:643px;top:80px"></span>
  <span class="abs social-name" style="left:661px;top:86px">Chirpline</span>
  <span class="abs social" style="left:643px;top:107px"></span>
  <span class="abs social-name" style="left:661px;top:113px">Friendwall</span>
  <span class="abs social" style="left:643px;top:134px"></span>
  <span class="abs social-name" style="left:661px;top:139px">Worknet</span>

  <div class="abs rule"></div>
  <p class="abs copyright">Copyright ©2013 Company Name &nbsp; - All rights reserved</p>
</footer>

</body>
</html>
```